Sales presentation introduction for Finance and Tech firms

Our business is two fold - 1) recruitment 2) consultancy. We would like a one or two page template that we can use to send to potential clients. The template will ideally be the same for the recruitment and consultancy side. We need to be able to edit the template to enter text.

I have attached our logo so you can see what we currently use on Corvella.

Sector is financial services and technology. We do not intent to have lots of text but the layout/images/designs to be used should cover some of page in a way that it takes up some space to avoid having to write lot of text.

Open to colour suggestions.

Please look at the attached word doc to see the text I would like for the two presentations.

Happy to answer questions.

Target Market(s)

Directors

Industry/Entity Type

Finance and tech companies

Colors
0094D4
00A9DD
6FCCEA
C7EBF8
E9F6FB

Requirements
Must have
• Editable text

```html
<!DOCTYPE html>
<html lang="en">
<head>
<meta charset="utf-8">
<title>Veridan – Sales Introduction</title>
<link rel="stylesheet" href="https://fonts.googleapis.com/css2?family=Roboto:wght@300;400;500;700&family=Roboto+Condensed:wght@400;700&family=Montserrat:wght@400&display=swap">
<style>
:root{
  --navy:#1d3461;
  --navy-deep:#16294f;
  --blue:#1565b4;
  --blue-mid:#2f86d0;
  --sky:#6fc3ec;
  --sky-pale:#c7ebf8;
  --ink:#222;
  --grey-logo:#7a7a7a;
  --stage:#e7ecf2;
  --white:#fff;
}
*{box-sizing:border-box;margin:0;padding:0}
html,body{width:1200px;height:2691px;overflow:hidden}
body{background:var(--stage);position:relative;font-family:"Roboto",sans-serif;color:var(--ink)}
.page{position:absolute;left:149px;width:873px;background:var(--white);overflow:hidden;box-shadow:6px 8px 14px rgba(0,0,0,.25)}
.page--intro{top:200px;height:1130px}
.page--services{top:1433px;height:1129px}
.abs{position:absolute}

/* header of intro page */
.intro-header{left:0;top:0;width:873px;height:425px}
.brand{display:flex;align-items:center;gap:12px;font-family:"Roboto",sans-serif;font-weight:300;color:var(--grey-logo)}
.brand__mark{width:22px;height:22px;background:var(--blue)}
.brand--top{left:62px;top:160px;font-size:50px}
.tagline{left:50px;top:313px;color:var(--white);font-family:"Roboto Condensed",sans-serif;font-weight:700}
.tagline__lead{font-size:21px;line-height:25px}
.tagline__claim{font-size:28px;line-height:34px;margin-top:6px}
.sky-stripe{left:0;top:427px;width:873px;height:18px;background:var(--sky)}

.intro-title{left:48px;top:468px;font-family:"Roboto Condensed",sans-serif;font-weight:700;font-size:31px;color:#2a2a2a}
.intro-body{left:51px;top:497px;width:788px;font-size:16px;line-height:25.7px;text-align:justify}

.checklist{left:54px;top:711px;list-style:none}
.checklist li{display:flex;align-items:center;gap:9px;font-family:"Roboto",sans-serif;font-weight:500;font-size:16.5px;line-height:25.7px;color:var(--navy)}
.checklist li:nth-child(6){margin-top:8px}
.tick{width:18px;height:16px;flex:none}

.team-photo{left:356px;top:678px;width:517px;height:372px}

.phone-band{display:flex;align-items:center;gap:14px;color:var(--white);font-size:37px;font-weight:500;padding-left:64px}
.phone-band svg{width:28px;height:28px}
.phone-band--intro{left:0;top:984px;width:356px;height:66px;background:var(--navy);clip-path:polygon(0 0,100% 0,91% 100%,0 100%)}

.footer{left:0;width:873px;height:55px}
.footer__address{position:absolute;left:49px;top:15px;color:var(--white);font-family:"Montserrat",sans-serif;font-size:19px}
.footer__contact{position:absolute;left:624px;top:12px;color:var(--white);font-family:"Montserrat",sans-serif;font-size:13.5px;line-height:15px}

/* services page */
.hero{left:0;top:0;width:873px;height:405px}
.hero-text{color:var(--white)}
.hero-text__a{left:40px;top:65px;font-weight:300;font-size:58px}
.hero-text__b{left:96px;top:130px;font-weight:700;font-size:58px;letter-spacing:.5px}
.hero-text__c{left:56px;top:198px;font-weight:300;font-size:35px}
.hero-text__d{left:89px;top:239px;font-family:"Roboto Condensed",sans-serif;font-weight:700;font-size:31px}

.service{width:350px}
.service h2{font-family:"Roboto",sans-serif;font-weight:700;font-size:30px;color:var(--blue);margin-bottom:18px;line-height:36px}
.service p{font-size:16px;line-height:25.8px;text-align:justify}
.service--strategy{left:41px;top:440px}
.service--change{left:425px;top:438px;width:410px}
.service--it{left:41px;top:709px}
.service--org{left:425px;top:707px;width:410px}

.brand--bottom{left:50px;top:985px;font-size:38px}
.phone-band--services{left:534px;top:991px;width:339px;height:66px;background:var(--navy);clip-path:polygon(0 0,100% 0,100% 100%,9% 100%);padding-left:66px}
</style>
</head>
<body>

<!-- Page one: firm introduction -->
<section class="page page--intro">
  <svg class="abs intro-header" viewBox="0 0 873 425" aria-hidden="true">
    <polygon points="300,0 873,0 873,425 520,425" fill="#9fb4c9"/>
    <polygon points="265,0 300,0 520,425 480,425" fill="#1a5ca8"/>
    <polygon points="200,302 370,175 470,302" fill="#2a82cf"/>
    <polygon points="230,302 330,230 300,302" fill="#6fc3ec"/>
    <polygon points="0,302 720,302 690,425 0,425" fill="#1d3461" opacity=".93"/>
    <polygon points="90,425 720,425 712,418 100,418" fill="#6fc3ec"/>
  </svg>
  <svg class="abs" style="left:330px;top:0;width:543px;height:302px" role="img" aria-label="Photo of a business team meeting around a table in a bright office" viewBox="0 0 543 302" preserveAspectRatio="none">
    <defs><linearGradient id="meet" x1="0" y1="0" x2="1" y2="1"><stop offset="0" stop-color="#dfe6ee"/><stop offset=".6" stop-color="#a9b9c9"/><stop offset="1" stop-color="#6f7f90"/></linearGradient></defs>
    <polygon points="0,0 543,0 543,302 160,302" fill="url(#meet)"/>
  </svg>
  <svg class="abs" style="left:720px;top:302px;width:153px;height:123px" role="img" aria-label="Continuation of the meeting photo" viewBox="0 0 153 123" preserveAspectRatio="none">
    <polygon points="0,0 153,0 153,123 -30,123" fill="#8797a8"/>
  </svg>

  <div class="abs brand brand--top"><span class="brand__mark"></span>VERIDAN</div>

  <div class="abs tagline">
    <p class="tagline__lead">A partner who brings new and innovative ideas to the table,<br>through extensive industry experience and knowledge.</p>
    <p class="tagline__claim">Veridan will ensure you are prepared for growth.</p>
  </div>
  <div class="abs sky-stripe"></div>

  <h1 class="abs intro-title">Veridan Consultancy</h1>
  <div class="abs intro-body">
    <p>Veridan is a bespoke consultancy firm that specialises in buy side investment. Through an industry based consultative approach we assist our clients in preparing for, and facilitating, long term growth. Working closely with our clients we combine innovative thinking and breakthrough technologies to accelerate progress and, together, achieve enduring results.</p>
    <p>Experienced in successfully delivering change for global organisations as well as assisting smaller firms during their growth phase. Veridan will work with you create a workable model and ensure successful delivery of the project.</p>
  </div>

  <ul class="abs checklist">
    <li><svg class="tick" viewBox="0 0 18 16"><path d="M1 9l5 5L17 1" fill="none" stroke="#1d3461" stroke-width="3"/></svg>Order Management and Trading</li>
    <li><svg class="tick" viewBox="0 0 18 16"><path d="M1 9l5 5L17 1" fill="none" stroke="#1d3461" stroke-width="3"/></svg>Investment and Research</li>
    <li><svg class="tick" viewBox="0 0 18 16"><path d="M1 9l5 5L17 1" fill="none" stroke="#1d3461" stroke-width="3"/></svg>Static, Pricing and Benchmark Data</li>
    <li><svg class="tick" viewBox="0 0 18 16"><path d="M1 9l5 5L17 1" fill="none" stroke="#1d3461" stroke-width="3"/></svg>CRM/ Onboarding</li>
    <li><svg class="tick" viewBox="0 0 18 16"><path d="M1 9l5 5L17 1" fill="none" stroke="#1d3461" stroke-width="3"/></svg>Performance, Risk and Attribution</li>
    <li><svg class="tick" viewBox="0 0 18 16"><path d="M1 9l5 5L17 1" fill="none" stroke="#1d3461" stroke-width="3"/></svg>Client and Regulatory Reporting</li>
    <li><svg class="tick" viewBox="0 0 18 16"><path d="M1 9l5 5L17 1" fill="none" stroke="#1d3461" stroke-width="3"/></svg>Compliance</li>
    <li><svg class="tick" viewBox="0 0 18 16"><path d="M1 9l5 5L17 1" fill="none" stroke="#1d3461" stroke-width="3"/></svg>Finance and Accounting</li>
    <li><svg class="tick" viewBox="0 0 18 16"><path d="M1 9l5 5L17 1" fill="none" stroke="#1d3461" stroke-width="3"/></svg>Middle and Back Office</li>
  </ul>

  <div class="abs team-photo" role="img" aria-label="Photo of a smiling business team giving thumbs up" style="background:linear-gradient(135deg,#eef2f6 0%,#c9d2dc 45%,#5a6470 100%)"></div>

  <div class="abs phone-band phone-band--intro">
    <svg viewBox="0 0 24 24" fill="none" stroke="#fff" stroke-width="1.6"><path d="M5 3h4l2 5-2.5 1.5a11 11 0 0 0 6 6L16 13l5 2v4a2 2 0 0 1-2 2A16 16 0 0 1 3 5a2 2 0 0 1 2-2z"/><path d="M14 3a7 7 0 0 1 7 7M14 7a3 3 0 0 1 3 3"/></svg>
    5550134782
  </div>

  <div class="abs footer" style="top:1050px">
    <svg class="abs" style="left:0;top:0" width="873" height="55" viewBox="0 0 873 55" aria-hidden="true">
      <polygon points="0,0 470,0 498,55 0,55" fill="#1d3461"/>
      <polygon points="480,0 505,0 533,55 508,55" fill="#c7d3ea"/>
      <polygon points="510,0 540,0 568,55 538,55" fill="#8a9ccf"/>
      <polygon points="545,0 873,0 873,55 573,55" fill="#1565b4"/>
    </svg>
    <p class="footer__address">18 Harrowgate Road Albany, NY 12203</p>
    <p class="footer__contact">info@veridanpartners.com<br>www.veridanpartners.com</p>
  </div>
</section>

<!-- Page two: services -->
<section class="page page--services">
  <div class="abs hero" role="img" aria-label="Photo of a businessman drawing a rising financial chart on a digital screen" style="background:linear-gradient(100deg,#3b86b0 0%,#2c6f9a 40%,#1c4a72 70%,#274a6e 100%)"></div>
  <svg class="abs" style="left:260px;top:190px;width:520px;height:170px" viewBox="0 0 520 170" aria-hidden="true">
    <polyline points="0,150 80,150 110,110 140,150 200,140 250,60 300,120 340,40 400,30 470,120 520,150" fill="none" stroke="#bfeaff" stroke-width="2.5"/>
  </svg>
  <p class="abs hero-text hero-text__a">Business Strategy</p>
  <p class="abs hero-text hero-text__b">MANAGEMENT</p>
  <p class="abs hero-text hero-text__c">IT TRANSFORMATION</p>
  <p class="abs hero-text hero-text__d">Organisational structure</p>

  <article class="abs service service--strategy">
    <h2>Business Strategy</h2>
    <p>Veridan will help you create a business strategy tailored to your requirements. Ensuing each business process is defined and taken into account allows for a successful design. Creating and implementing an operating model that takes into account budget, resources, culture and your company’s vision.</p>
  </article>
  <article class="abs service service--change">
    <h2>Change management</h2>
    <p>Veridan works with clients to deliver bespoke change initiatives. Rigorous business analysis and risk management allows for successful change initiatives. We work with you throughout the complete process, to ensure that delivery is based on value. Transition phases are challenging aspects of change initiatives which is why our team manage all transitions and the risk they carry.</p>
  </article>
  <article class="abs service service--it">
    <h2>IT transformation</h2>
    <p>Veridan is widely experienced in a range of technologies. We help with the implementation of software provider or design and develop bespoke services. Covering front to back office the team specialises in full project lifecycle from feasibility through to implementation.</p>
  </article>
  <article class="abs service service--org">
    <h2>Organisational structure</h2>
    <p>Veridan works with clients to improve resource capability and strategic partnerships. Acting as an extension of the HR function, we analyse business processes and ensure that our clients have the ability to manage changing workforce demands.</p>
  </article>

  <div class="abs brand brand--bottom"><span class="brand__mark"></span>VERIDAN</div>

  <div class="abs phone-band phone-band--services">
    <svg viewBox="0 0 24 24" fill="none" stroke="#fff" stroke-width="1.6"><path d="M5 3h4l2 5-2.5 1.5a11 11 0 0 0 6 6L16 13l5 2v4a2 2 0 0 1-2 2A16 16 0 0 1 3 5a2 2 0 0 1 2-2z"/><path d="M14 3a7 7 0 0 1 7 7M14 7a3 3 0 0 1 3 3"/></svg>
    5550134782
  </div>

  <div class="abs footer" style="top:1055px">
    <svg class="abs" style="left:0;top:0" width="873" height="55" viewBox="0 0 873 55" aria-hidden="true">
      <polygon points="0,0 470,0 498,55 0,55" fill="#1d3461"/>
      <polygon points="480,0 505,0 533,55 508,55" fill="#c7d3ea"/>
      <polygon points="510,0 540,0 568,55 538,55" fill="#8a9ccf"/>
      <polygon points="545,0 873,0 873,55 573,55" fill="#1565b4"/>
    </svg>
    <p class="footer__address">18 Harrowgate Road Albany, NY 12203</p>
    <p class="footer__contact">info@veridanpartners.com<br>www.veridanpartners.com</p>
  </div>
</section>

</body>
</html>
```